Freelance business trainer needs a new business card

My business is called Brontlearn. I provide training in the workplace on management, coaching and mentoring, and customer service topics for a variety of businesses, colleges and private training providers, and teach on management programs. I need a professional but eye catching business card. Business colours grey and orange. My name Marion Tadwick; Tel 07382 415067; email mtadwick@brontlearn.co.uk; website www.brontlearn.co.uk.
Happy to have some sort of logo on front and details on back or all on one side
Target Market(s)
SME businesses and colleges - workshops i run are for adults in the workplace
Industry/Entity Type
Training
Look and feel

```html
<!DOCTYPE html>
<html lang="en">
<head>
<meta charset="utf-8">
<title>Brontlearn – Business Card</title>
<link rel="stylesheet" href="https://fonts.googleapis.com/css2?family=Roboto:wght@400&family=Ubuntu:wght@400&display=swap">
<style>
  :root {
    --page-bg: #e9e9ec;
    --card-top: #f4f3f0;
    --card-mid: #fbfbf9;
    --card-bottom: #ecebe7;
    --orange: #e37418;
    --grey-text: #5b5d60;
    --contact-text: #555759;
    --band-white: #fdfdfc;
  }

  * { margin: 0; padding: 0; box-sizing: border-box; }

  html, body {
    width: 1200px;
    height: 800px;
    overflow: hidden;
    background: var(--page-bg);
  }

  .canvas {
    position: relative;
    width: 1200px;
    height: 800px;
  }

  .business-card {
    position: absolute;
    left: 75px;
    top: 100px;
    width: 1050px;
    height: 600px;
    background: linear-gradient(160deg, var(--card-top) 0%, var(--card-mid) 45%, var(--card-bottom) 100%);
    box-shadow: 0 6px 24px rgba(0, 0, 0, 0.12);
    overflow: hidden;
  }

  .accent-line {
    position: absolute;
    top: 0;
    width: 5px;
    height: 305px;
    background: var(--orange);
  }
  .accent-line--first { left: 282px; }
  .accent-line--second { left: 300px; }

  .brand {
    position: absolute;
    left: 110px;
    top: 326px;
  }

  .brand__name {
    font-family: "Ubuntu", sans-serif;
    font-weight: 400;
    font-size: 58px;
    line-height: 1;
    color: var(--grey-text);
    letter-spacing: 0.5px;
  }

  .name-band {
    position: absolute;
    left: 560px;
    top: 190px;
    width: 490px;
    height: 64px;
    background: var(--band-white);
    display: flex;
    align-items: center;
    padding-left: 32px;
    box-shadow: -4px 14px 14px -10px rgba(0, 0, 0, 0.55);
  }

  .name-band__name {
    font-family: "Ubuntu", sans-serif;
    font-weight: 400;
    font-size: 31px;
    color: var(--orange);
    letter-spacing: 0.5px;
  }

  .contact-list {
    position: absolute;
    left: 588px;
    top: 318px;
    list-style: none;
  }

  .contact-item {
    display: flex;
    align-items: center;
    height: 56px;
  }

  .contact-item__icon {
    width: 30px;
    height: 30px;
    margin-right: 30px;
    fill: var(--orange);
  }

  .contact-item__text {
    font-family: "Roboto", sans-serif;
    font-size: 28px;
    color: var(--contact-text);
    letter-spacing: 1px;
  }
</style>
</head>
<body>
<main class="canvas">
  <article class="business-card">
    <span class="accent-line accent-line--first"></span>
    <span class="accent-line accent-line--second"></span>

    <div class="brand">
      <span class="brand__name">Brontlearn</span>
    </div>

    <div class="name-band">
      <span class="name-band__name">Marion Tadwick</span>
    </div>

    <ul class="contact-list">
      <li class="contact-item">
        <svg class="contact-item__icon" viewBox="0 0 30 30" aria-hidden="true">
          <path d="M4 9c0-3 5-5 11-5s11 2 11 5v2h-6V8.5c-3-1-7-1-10 0V11H4z"/>
          <path d="M9 12h12l4 11H5z"/>
        </svg>
        <span class="contact-item__text">07382 415067</span>
      </li>
      <li class="contact-item">
        <svg class="contact-item__icon" viewBox="0 0 30 30" aria-hidden="true">
          <path d="M2 7h26v16H2z"/>
          <path d="M2 7l13 10L28 7" fill="none" stroke="#fbfbf9" stroke-width="2"/>
        </svg>
        <span class="contact-item__text">mtadwick@brontlearn.co.uk</span>
      </li>
      <li class="contact-item">
        <svg class="contact-item__icon" viewBox="0 0 30 30" aria-hidden="true">
          <circle cx="15" cy="15" r="12"/>
          <g fill="none" stroke="#fbfbf9" stroke-width="1.6">
            <ellipse cx="15" cy="15" rx="5" ry="12"/>
            <path d="M3 15h24M5 9h20M5 21h20M15 3v24"/>
          </g>
        </svg>
        <span class="contact-item__text">www.brontlearn.co.uk.</span>
      </li>
    </ul>
  </article>
</main>
</body>
</html>
```